Business Card Design for a Software Startup

We'd like to have a business card design. We already have a logo. Basically what we need is a clean design with name, address, cellphone and phone numbers, e-mail and web site address (front) and a space on the back with our logo with the company name on the right side and some texts on the bottom.
We are a development and consulting company in Brazil with highly qualified team of professionals in Java, iOS and Android development and consulting.

Target Market(s)

CIO, IT managers of mid to big size companies

Industry/Entity Type

Business

```html
<!DOCTYPE html>
<html lang="en">
<head>
<meta charset="utf-8">
<title>Kreldo Business Card</title>
<link rel="stylesheet" href="https://fonts.googleapis.com/css2?family=Ubuntu:wght@400;500;700&display=swap">
<style>
  :root {
    --stage: #e6e6ec;
    --navy: #0b3f6e;
    --navy-deep: #072f55;
    --sky: #1f8fcf;
    --ink: #2a2a2a;
    --muted: #555;
    --paper: #ffffff;
    --rule: #c9ccd3;
  }
  * { margin: 0; padding: 0; box-sizing: border-box; }
  html, body { width: 1200px; height: 987px; overflow: hidden; }
  body {
    background: var(--stage);
    font-family: "Ubuntu", sans-serif;
    position: relative;
  }
  .card {
    position: absolute;
    width: 700px;
    height: 400px;
    border-radius: 28px;
    overflow: hidden;
  }
  /* Back side */
  .card-back {
    left: 440px; top: 60px;
    background: linear-gradient(160deg, var(--navy) 0%, var(--navy-deep) 100%);
    color: var(--paper);
  }
  .card-back .brand-name {
    position: absolute;
    left: 0; right: 0; top: 120px;
    text-align: center;
    font-size: 104px;
    font-weight: 700;
    letter-spacing: 2px;
    line-height: 1.1;
    color: var(--paper);
  }
  .card-back .web {
    position: absolute;
    left: 0; right: 0; top: 262px;
    text-align: center;
    font-size: 22px;
    font-weight: 500;
    letter-spacing: 6px;
    color: var(--paper);
  }
  /* Front side */
  .card-front {
    left: 60px; top: 527px;
    background: var(--paper);
  }
  .swoosh { position: absolute; inset: 0; }
  .logo-block {
    position: absolute;
    left: 70px; top: 45px;
    width: 230px;
    text-align: center;
  }
  .logo-square {
    display: block;
    width: 104px; height: 104px;
    margin: 0 auto 8px;
    border-radius: 14px;
    background: var(--navy);
  }
  .logo-block .brand-name {
    font-size: 44px;
    font-weight: 700;
    line-height: 1.1;
    color: var(--navy);
    letter-spacing: 1px;
  }
  .divider {
    position: absolute;
    left: 320px; top: 50px;
    width: 1px; height: 200px;
    background: var(--rule);
  }
  .person {
    position: absolute;
    left: 350px; top: 48px;
  }
  .person-name {
    font-size: 32px;
    font-weight: 700;
    color: var(--navy);
    line-height: 1;
  }
  .person-title {
    font-size: 19px;
    color: var(--muted);
    margin-top: 4px;
  }
  .contacts {
    list-style: none;
    margin-top: 20px;
  }
  .contacts li {
    display: flex;
    align-items: center;
    gap: 10px;
    font-size: 20px;
    color: var(--ink);
    line-height: 30px;
  }
  .contacts svg { width: 16px; height: 16px; flex: none; }
  .address {
    position: absolute;
    right: 300px; bottom: 22px;
    text-align right;
    text-align: right;
    color: var(--paper);
    font-size: 18px;
    line-height: 24px;
  }
</style>
</head>
<body>

<section class="card card-back">
  <div class="brand-name">KRELDO</div>
  <div class="web">www.kreldo-dev.com</div>
</section>

<section class="card card-front">
  <svg class="swoosh" viewBox="0 0 700 400" width="700" height="400" aria-hidden="true">
    <defs>
      <linearGradient id="band" x1="0" y1="0" x2="1" y2="0">
        <stop offset="0" stop-color="#0d4a80"/>
        <stop offset="1" stop-color="#072f55"/>
      </linearGradient>
    </defs>
    <path d="M0,258 C200,295 430,325 700,400 L0,400 Z" fill="url(#band)"/>
    <path d="M0,248 C205,283 440,308 700,384" fill="none" stroke="#1f8fcf" stroke-width="3"/>
  </svg>

  <div class="logo-block">
    <span class="logo-square"></span>
    <div class="brand-name">KRELDO</div>
  </div>

  <div class="divider"></div>

  <div class="person">
    <div class="person-name">Your Name</div>
    <div class="person-title">Title</div>
    <ul class="contacts">
      <li>
        <svg viewBox="0 0 16 16"><circle cx="8" cy="8" r="8" fill="#0b3f6e"/><path d="M5 4.5l2 2-1 1a5 5 0 0 0 2.5 2.5l1-1 2 2-1.2 1.2C7.5 12 4 8.5 3.8 5.7z" fill="#fff"/></svg>
        123-456-7890
      </li>
      <li>
        <svg viewBox="0 0 16 16"><rect x="4" y="1" width="8" height="14" rx="1.5" fill="#0b3f6e"/><rect x="5.5" y="3" width="5" height="5" fill="#fff"/></svg>
        456-085-4321
      </li>
      <li>
        <svg viewBox="0 0 16 16"><rect x="1" y="3" width="14" height="10" rx="1" fill="#0b3f6e"/><path d="M1.5 3.8L8 9l6.5-5.2" fill="none" stroke="#fff" stroke-width="1.2"/></svg>
        yourname@kreldo-dev.com
      </li>
      <li>
        <svg viewBox="0 0 16 16"><circle cx="8" cy="8" r="7" fill="#0b3f6e"/><path d="M1 8h14M8 1c-3 3.5-3 10.5 0 14M8 1c3 3.5 3 10.5 0 14" fill="none" stroke="#fff" stroke-width="1"/></svg>
        www.kreldo-dev.com
      </li>
    </ul>
  </div>

  <div class="address">
    Door No. Street Name<br>
    City Name, State, Zip Code
  </div>
</section>

</body>
</html>
```